Deskside Thrive Fliers and logo design

We need to design a product logo and some informational fliers for a vigour quest.
I have attached our Deskside Thrive logo - colours need to be complimentary but not the same, we would like fresh, funky but still professional. We generally communicate in a fairly casual way to reach our market. (We don't like boring)
Clear and simple - not too busy
images are good but not actual photos
Here is our website to give you an idea www.desksidethrive.co.nz
The flier is a 3 page document.
The logo is to say Vigour Quest. The challenge is based on exercise, connecting with people, giving, learning and taking notice (The 7 paths to flourishing) Once agin the logo needs to be complementary but not the same.
The Deskside thrive logo needs to be on the fliers but the vigour quest logo is separate.
Thanks very much!!

```html
<!DOCTYPE html>
<html lang="en">
<head>
<meta charset="utf-8">
<title>Stress Buster! – Vigour Quest</title>
<link href="https://fonts.googleapis.com/css2?family=Roboto:wght@400;500;700;900&display=swap" rel="stylesheet">
<style>
  :root {
    --teal: #0b6d67;
    --teal-bright: #27ad98;
    --orange: #e05837;
    --green: #8cbf45;
    --green-soft: #a7cd58;
    --ink: #222;
    --white: #fff;
  }
  * { box-sizing: border-box; margin: 0; padding: 0; }
  html, body { width: 928px; height: 1200px; overflow: hidden; background: var(--white); }
  body { font-family: "Roboto", Arial, sans-serif; color: var(--ink); }
  .flier { position: relative; width: 928px; height: 1200px; overflow: hidden; background: var(--white); }
  .backdrop { position: absolute; inset: 0; }

  .quest-logo { position: absolute; left: 36px; top: 46px; display: flex; align-items: center; gap: 14px; }
  .quest-logo .dot { width: 56px; height: 56px; border-radius: 50%; background: var(--green); }
  .quest-logo .name { font-weight: 900; font-size: 46px; color: var(--teal-bright); letter-spacing: 1px; line-height: 1; }

  .host-logo { position: absolute; left: 612px; top: 30px; width: 200px; text-align: left; }
  .host-logo .dot { width: 34px; height: 34px; border-radius: 50%; background: var(--orange); margin: 0 0 6px 120px; }
  .host-logo .name { font-weight: 700; font-size: 36px; line-height: 34px; color: var(--teal-bright); letter-spacing: -0.5px; }

  .headline { position: absolute; left: 34px; top: 150px; color: var(--white); font-weight: 900; font-size: 101px; line-height: 82px; letter-spacing: -3px; }
  .tagline { position: absolute; left: 36px; top: 311px; width: 380px; color: var(--white); font-weight: 700; font-size: 22.5px; line-height: 28px; }
  .intro { position: absolute; left: 469px; top: 194px; width: 425px; color: var(--white); font-weight: 700; font-size: 11.3px; line-height: 14.4px; }
  .intro p { margin-bottom: 6px; }

  .step { position: absolute; left: 44px; width: 840px; display: flex; align-items: flex-start; }
  .step .tag { flex: none; width: 174px; height: 40px; background: var(--orange); color: var(--white);
    font-weight: 700; font-size: 24px; line-height: 40px; padding-left: 10px;
    clip-path: polygon(0 5px, 150px 5px, 150px 0, 174px 20px, 150px 40px, 150px 35px, 0 35px); }
  .step .text { font-size: 14.6px; line-height: 18px; padding: 11px 0 0 12px; }
  .step-s { top: 426px; } .step-t { top: 466px; } .step-o { top: 507px; } .step-p { top: 613px; }

  .observe { position: absolute; top: 544px; height: 69px; background: var(--green-soft); padding: 3px 9px; }
  .observe h3 { font-weight: 700; font-size: 16.5px; line-height: 18px; color: #1c1c1c; }
  .observe p { font-size: 11.3px; line-height: 14px; color: #2f3a1d; }
  .obs-body { left: 226px; width: 196px; } .obs-emotions { left: 430px; width: 147px; } .obs-mind { left: 588px; width: 296px; }

  .values-intro { position: absolute; left: 44px; top: 690px; width: 208px; height: 470px; background: var(--teal); color: var(--white); padding: 33px 10px 0 11px; }
  .values-intro h2 { font-weight: 700; font-size: 21px; line-height: 22px; }
  .values-intro p { font-size: 14.5px; line-height: 17.6px; }
  .values-intro h4 { font-weight: 700; font-size: 17px; line-height: 22px; margin: 18px 0 26px; }

  .values-panel { position: absolute; left: 252px; top: 674px; width: 632px; height: 490px; border: 6px solid var(--teal); background: var(--white); }
  .values-list { position: absolute; top: 6px; list-style: none; font-size: 12.4px; line-height: 16.4px; color: #2a2a2a; }
  .col-1 { left: 14px; } .col-2 { left: 226px; } .col-3 { left: 418px; }
</style>
</head>
<body>
<div class="flier">
  <svg class="backdrop" width="928" height="1200" viewBox="0 0 928 1200" aria-hidden="true">
    <rect x="0" y="122" width="560" height="16" fill="#8cbf45"/>
    <rect x="0" y="152" width="928" height="252" fill="#0b6d67"/>
    <polygon points="346,403 426,403 386,426" fill="#0b6d67"/>
    <polygon points="606,0 928,0 928,166 502,166" fill="#fff"/>
    <polyline points="502,167 606,1" fill="none" stroke="#e05837" stroke-width="4"/>
    <line x1="502" y1="166" x2="928" y2="166" stroke="#e05837" stroke-width="4"/>
    <rect x="0" y="1100" width="928" height="100" fill="#8dc14a"/>
  </svg>

  <div class="quest-logo"><span class="dot"></span><span class="name">Vigour Quest</span></div>
  <div class="host-logo"><div class="dot"></div><div class="name">Deskside<br>thrive</div></div>

  <h1 class="headline">STRESS<br>BUSTER!</h1>
  <p class="tagline">We cannot control what happens to us in life, but we can change the way we react</p>

  <div class="intro">
    <p>Stress happens because we are allowing fear, anger, disappointment and a host of other negative emotions to navigate our actions. By becoming aware of these emotions and allowing them to simply be, we can begin to gain control of how we react and respond to stressful situations.</p>
    <p>Our experience is always changing. Without awareness, mental patterns related to what we fear and what upsets us make life harder.</p>
    <p>S.T.O.P is a powerful, yet surprisingly basic strategy that helps you to be focused, alert, relaxed and at your emotional best when stressful moments present themselves in your life.</p>
    <p>Simply put, it's a four-step checklist to use anytime you want to ground yourself and get some insight into whatever is going on. The whole idea behind it is that by taking a very brief break—even less than one minute—you can determine the very best action to take in the moment.</p>
  </div>

  <div class="step step-s"><div class="tag">S = Stop</div><div class="text">Stop what you are doing: Press the pause button on your thoughts and actions.</div></div>
  <div class="step step-t"><div class="tag">T = Take</div><div class="text">Take a few deep breaths to centre yourself and bring yourself fully into the present moment.</div></div>
  <div class="step step-o"><div class="tag">O = Observe</div><div class="text">Observe what is going on with your:</div></div>

  <div class="observe obs-body"><h3>BODY</h3><p>What physical sensations are you aware of (touch, sight, hearing, taste, smell)?</p></div>
  <div class="observe obs-emotions"><h3>EMOTIONS</h3><p>What are you feeling right now?</p></div>
  <div class="observe obs-mind"><h3>MIND</h3><p>What assumptions are your making about your feelings? What is the story you're telling yourself about why you are having them?</p></div>

  <div class="step step-p"><div class="tag">P = Proceed</div><div class="text">Proceed with whatever you were doing, making a conscious, intentional choice to incorporate what you just learned.</div></div>

  <div class="values-intro">
    <h2>VALUES</h2>
    <p>This exercise is designed to help you reach a better understanding of your most significant values.</p>
    <h4>STEP 1:<br>What I Value Most...</h4>
    <p>From this list of values (both work and personal), select the ten that are most important to you - as guides for how to behave, or as components of a valued way of life. Feel free to add any values of your own to this list.</p>
  </div>

  <div class="values-panel">
    <ul class="values-list col-1">
      <li>Achievement</li><li>Advancement and promotion</li><li>Adventure</li><li>Affection (love and caring)</li><li>Arts</li><li>Challenging problems</li><li>Change and variety</li><li>Close relationships</li><li>Community</li><li>Competence</li><li>Competition</li><li>Cooperation</li><li>Country</li><li>Creativity</li><li>Decisiveness</li><li>Democracy</li><li>Ecological awareness</li><li>Economic security</li><li>Effectiveness</li><li>Efficiency</li><li>Ethical practice</li><li>Excellence</li><li>Excitement</li><li>Fame</li><li>Fast living</li><li>Financial gain</li><li>Freedom</li>
    </ul>
    <ul class="values-list col-2">
      <li>Friendships</li><li>Growth</li><li>Having a family</li><li>Helping other people</li><li>Helping society</li><li>Honesty</li><li>Independence</li><li>Influencing others</li><li>Inner harmony</li><li>Integrity</li><li>Intellectual status</li><li>Involvement</li><li>Job tranquility</li><li>Knowledge</li><li>Leadership</li><li>Location</li><li>Loyalty</li><li>Market position</li><li>Meaningful work</li><li>Merit</li><li>Money</li><li>Nature</li><li>Being around people who<br>are open and honest</li><li>Order (tranquility,<br>stability, conformity)</li><li>Personal development</li>
    </ul>
    <ul class="values-list col-3">
      <li>Physical challenge</li><li>Pleasure</li><li>Power and authority</li><li>Privacy</li><li>Public service</li><li>Purity</li><li>Quality of what I take part in</li><li>Quality relationships</li><li>Recognition (respect from<br>others, status)</li><li>Religion</li><li>Reputation</li><li>Responsibility and accountability</li><li>Security</li><li>Self-Respect</li><li>Serenity</li><li>Sophistication</li><li>Stability</li><li>Status</li><li>Supervising others</li><li>Time freedom</li><li>Truth</li><li>Wealth</li><li>Wisdom</li><li>Work under pressure</li><li>Work with others</li><li>Working alone</li>
    </ul>
  </div>
</div>
</body>
</html>
```